Website design with eCommerce for revolutionary new product in the manufacturing industry.

We need a website designed for a precision manufacturing company based in the suburbs of Minneapolis, Minnesota called Velkrin Manufacturing. We have a revolutionary new product, the TARN LOCK, to introduce and sell through an eCommerce storefront. The website would include company information, product information, and the storefront. Green is a color that represents Velkrin Manufacturing. The final design should communicate that we exclusively offer premium products at a premium price. The design should also let the customer know they are the focus of our work.

Target Market(s)

Machinists and machine shops

Industry/Entity Type

Manufacturing and machine shops

Coding

Coded - Design and coding required

Font styles to use
Sans Serif

Colors
59FF00
82FF00
B8FF75
E3FFCB
F4FFEA

Requirements
Must have
• eCommerce storefront, Made in USA references
Nice to have
• Home page, TARN LOCK Product page, About Us, Capabilities, Contact, etc.
Should not have
• Should not be too much text and reading.

```html
<!DOCTYPE html>
<html lang="en">
<head>
<meta charset="utf-8">
<title>Velkrin Manufacturing – TARN LOCK website pages</title>
<link href="https://fonts.googleapis.com/css2?family=Orbitron:wght@700;800;900&family=Poppins:ital,wght@0,400;0,500;0,600;0,700;1,400&display=swap" rel="stylesheet">
<style>
:root{
  --green:#59ff00;
  --green-2:#82ff00;
  --green-soft:#b8ff75;
  --ink:#141414;
  --ink-2:#1b1b1b;
  --ink-3:#232323;
  --ink-4:#2c2c2c;
  --line:#3a3a3a;
  --text:#ffffff;
  --muted:#b9b9b9;
  --stage:#d6d6d6;
  --stage-light:#f2f2f2;
  --product-hi:#3fcf1a;
  --product-mid:#22921a;
  --product-lo:#0f4d09;
}
*{margin:0;padding:0;box-sizing:border-box}
html,body{width:1200px;height:2537px;overflow:hidden}
body{position:relative;background:var(--stage);font-family:'Poppins',sans-serif;color:var(--text)}
.stage-bands{position:absolute;inset:0}
.head{font-family:'Orbitron',sans-serif;font-weight:800;letter-spacing:.03em;text-transform:uppercase}
.page{position:absolute;width:396px;background:var(--ink);overflow:hidden;box-shadow:0 18px 40px rgba(0,0,0,.35)}
.page>*{position:absolute}
/* nav */
.nav{top:0;left:0;width:396px;height:26px;background:var(--ink);display:flex;align-items:center;z-index:5}
.brand{font-family:'Orbitron',sans-serif;font-weight:800;font-size:8px;color:var(--text);margin-left:30px;width:74px;letter-spacing:.02em}
.nav-links{display:flex;gap:6px;font-size:3.4px;font-weight:600;color:var(--text);flex:1}
.nav-links .on{color:var(--green)}
.nav-cta{width:34px;height:26px;background:var(--green);color:var(--ink);font-size:3.6px;font-weight:700;display:flex;align-items:center;justify-content:center}
/* hero */
.hero{top:25px;left:0;width:396px;height:135px}
.hero-photo{position:absolute;inset:0;background:
  linear-gradient(115deg,rgba(255,255,255,.08) 0 18%,rgba(0,0,0,0) 18% 40%,rgba(255,255,255,.06) 40% 55%,rgba(0,0,0,0) 55%),
  linear-gradient(180deg,#4a4a4a 0%,#2a2a2a 55%,#161616 100%)}
.hero-photo.warm{background:
  linear-gradient(115deg,rgba(255,230,180,.08) 0 20%,rgba(0,0,0,0) 20% 45%,rgba(255,230,180,.06) 45% 60%,rgba(0,0,0,0) 60%),
  linear-gradient(180deg,#5c5040 0%,#3a3226 55%,#1a1712 100%)}
.hero-cut{position:absolute;inset:0;width:100%;height:100%}
.hero-title{position:absolute;left:0;right:0;top:42px;text-align:center;font-size:19px;z-index:2}
/* product imagery */
.product-shot{border-radius:6px;background:linear-gradient(150deg,var(--product-hi) 0%,var(--product-mid) 45%,var(--product-lo) 100%);box-shadow:0 6px 14px rgba(0,0,0,.45)}
/* section text */
.h2{font-family:'Orbitron',sans-serif;font-weight:800;font-size:11.5px;text-transform:uppercase;letter-spacing:.03em;line-height:1.15}
.rule{display:block;width:14px;height:1.5px;background:var(--green);margin-top:4px}
.rule.center{margin-left:auto;margin-right:auto}
.small{font-size:4px;line-height:1.55;color:var(--muted)}
.ticks{list-style:none;font-size:4px;line-height:1.5;color:var(--muted)}
.ticks li{position:relative;padding-left:7px;margin-bottom:4px}
.ticks li::before{content:"";position:absolute;left:0;top:2px;width:2.6px;height:2.6px;border-radius:50%;background:var(--green)}
.ticks li.sub{margin-left:6px}
.ph{border-radius:2px}
.btn{background:var(--green);color:var(--ink);font-size:3.8px;font-weight:700;display:flex;align-items:center;justify-content:center;border-radius:1px}
/* footer */
.footer{left:0;bottom:0;width:396px;height:170px;background:#0f0f0f}
.footer>*{position:absolute}
.f-brand{top:10px;left:0;right:0;text-align:center;font-family:'Orbitron',sans-serif;font-weight:800;font-size:11px}
.f-col{top:42px;font-size:3.5px;color:var(--muted);line-height:1.7}
.f-col h4{font-family:'Orbitron',sans-serif;font-size:4.6px;color:var(--text);margin-bottom:6px;letter-spacing:.04em}
.f-soc{display:flex;align-items:center;gap:3px;margin-bottom:3.2px}
.f-soc i{width:5px;height:5px;border-radius:50%;background:#333;display:inline-block}
.f-mail{display:flex;gap:3px}
.f-mail i{width:4px;height:4px;background:var(--green);border-radius:1px;display:inline-block;margin-top:1px}
.f-input{width:86px;height:9px;background:#252525;font-size:3.3px;color:#aaa;padding-left:4px;display:flex;align-items:center;margin-bottom:4.5px}
.f-submit{width:30px;height:8px;background:#fff;color:var(--ink);font-size:3.3px;font-weight:700;display:flex;align-items:center;justify-content:center;margin-top:2px}
.f-line{left:30px;right:30px;bottom:18px;height:1px;background:#262626}
.f-copy{left:0;right:0;bottom:7px;text-align:center;font-size:3.5px;font-weight:600}
.f-up{right:15px;bottom:24px;width:13px;height:13px;background:var(--green);color:var(--ink);font-size:7px;display:flex;align-items:center;justify-content:center}
/* home */
.welcome{position:absolute;left:0;right:0;text-align:center;z-index:2}
.frame-line{background:#fff;z-index:2}
.card{background:var(--ink-3);border-radius:3px;padding:26px 11px 0;font-size:3.7px;line-height:1.6;color:var(--muted)}
.card-icon{position:absolute;top:-17px;left:50%;margin-left:-15px;width:30px;height:30px;background:var(--green);border-radius:3px}
.arrow-btn{width:10px;height:10px;border-radius:2px;background:#2a2a2a;font-size:5px;display:flex;align-items:center;justify-content:center;color:#fff}
.arrow-btn.on{background:var(--green);color:var(--ink)}
.caps{left:0;top:825px;width:396px;height:222px;background:linear-gradient(160deg,#222 0%,#1a1a1a 55%,#151515 100%)}
.cap-label{position:absolute;font-family:'Orbitron',sans-serif;font-weight:700;font-style:italic;font-size:4.4px;text-transform:uppercase;white-space:nowrap}
.cap-label.r{text-align:left}
.cap-label.l{text-align:right}
.cap-sub{display:block;font-family:'Poppins',sans-serif;font-style:normal;font-weight:400;text-transform:none;font-size:3.4px;color:var(--muted);line-height:1.4}
/* gallery */
.grid-cell{position:absolute;border-radius:2px}
/* wisdom */
.quote{background:var(--ink-3);border-radius:3px;text-align:center;padding:12px 10px 0}
.quote-mark{font-family:'Orbitron',sans-serif;font-size:16px;color:var(--green);line-height:1;height:12px}
.quote p{font-size:5px;font-style:italic;color:var(--muted);line-height:1.4;margin-top:4px;min-height:28px}
.quote cite{display:block;font-style:normal;font-size:3.8px;font-weight:700;color:var(--green);text-transform:uppercase}
/* contact */
.c-item{display:flex;align-items:center;gap:7px}
.c-icon{width:20px;height:20px;background:var(--green);border-radius:3px;display:flex;align-items:center;justify-content:center}
.c-item span{font-size:5.2px;color:var(--muted);line-height:1.2}
.c-item b{display:block;font-size:6.4px;color:var(--text);font-weight:600}
.f-label{font-size:3.2px;font-weight:700;color:var(--text)}
.c-field{background:#f3f3f3;color:#777;font-size:3.3px;padding-left:4px;display:flex;align-items:center;border-radius:1px}
</style>
</head>
<body>

<svg class="stage-bands" width="1200" height="2537" viewBox="0 0 1200 2537" aria-hidden="true">
  <polygon points="0,740 1200,100 1200,130 0,770" fill="var(--stage-light)" opacity=".9"/>
  <polygon points="560,1000 1200,530 1200,660 560,1130" fill="#ffffff"/>
  <polygon points="0,1400 560,1090 560,1230 0,1540" fill="#ffffff" opacity=".7"/>
  <polygon points="560,1720 1200,1290 1200,1420 560,1850" fill="#ffffff"/>
  <polygon points="0,2180 560,1880 560,2000 0,2300" fill="#ffffff" opacity=".7"/>
</svg>

<!-- ================= HOME ================= -->
<section class="page page-home" style="left:170px;top:130px;height:1461px">
  <nav class="nav">
    <div class="brand">TARN LOCK</div>
    <div class="nav-links"><span>WHY VELKRIN?</span><span>WHAT WE DO</span><span>HOW WE MAKE IT BETTER</span><span>CAPABILITIES</span><span>GALLERY</span><span>ABOUT US</span><span>WISDOM</span></div>
    <div class="nav-cta">CONTACT</div>
  </nav>

  <div class="hero" style="height:245px">
    <div class="hero-photo" role="img" aria-label="Close-up photo of stacked black machined rings"></div>
    <svg class="hero-cut" viewBox="0 0 396 245" preserveAspectRatio="none" aria-hidden="true">
      <polygon points="0,236 396,178 396,245 0,245" fill="var(--ink)"/>
      <polygon points="0,228 396,183 396,196 0,236" fill="var(--green)"/>
    </svg>
    <div class="frame-line" style="position:absolute;left:172px;top:36px;width:57px;height:3px"></div>
    <div class="frame-line" style="position:absolute;left:172px;top:36px;width:3px;height:22px"></div>
    <div class="frame-line" style="position:absolute;left:226px;top:36px;width:3px;height:22px"></div>
    <div class="welcome head" style="top:64px;font-size:15px">WELCOME TO</div>
    <div class="welcome head" style="top:86px;font-size:17px;color:var(--green)">VELKRIN</div>
    <div class="welcome head" style="top:112px;font-size:15px">MANUFACTURING</div>
    <div class="frame-line" style="position:absolute;left:172px;top:155px;width:3px;height:22px"></div>
    <div class="frame-line" style="position:absolute;left:226px;top:155px;width:3px;height:22px"></div>
    <div class="frame-line" style="position:absolute;left:172px;top:174px;width:57px;height:3px"></div>
  </div>

  <div class="ph" style="left:54px;top:290px;width:106px;height:137px;background:linear-gradient(150deg,#2b4e9c,#c89a5a 55%,#1f3f86)" role="img" aria-label="Photo of brass machined parts on a blue mat"></div>
  <div class="ph" style="left:117px;top:367px;width:70px;height:90px;background:linear-gradient(160deg,#d8c7a4,#8e7a56 50%,#e6dccb);border:2px solid var(--ink)" role="img" aria-label="Photo of rows of brass threaded fittings"></div>
  <div style="left:211px;top:323px;width:160px">
    <div class="h2">WHY VELKRIN<br>MANUFACTURING?</div><span class="rule"></span>
    <p class="small" style="margin-top:8px">Because there is a better way, and we will find it, even if it's the hard way.</p>
    <p class="small" style="margin-top:5px">Here's what we believe in:</p>
    <ul class="ticks" style="margin-top:5px">
      <li>We work smarter and harder to make you successful</li>
      <li>Our success is measured in your success</li>
      <li>It is always our goal to exceed your expectations</li>
    </ul>
  </div>

  <div style="left:30px;top:513px"><div class="h2">WHAT<br>WE DO</div><span class="rule"></span></div>
  <div class="arrow-btn" style="left:30px;top:557px">&larr;</div>
  <div class="arrow-btn" style="left:48px;top:557px">&rarr;</div>
  <div class="card" style="left:120px;top:505px;width:107px;height:82px"><div class="card-icon"></div>We are a machine shop with complete end to end manufacturing capabilities.</div>
  <div class="card" style="left:233px;top:505px;width:107px;height:82px"><div class="card-icon"></div>We will work with you at any stage of your product development, whether it is just an idea or a fully engineered project, to help find the best path to product realization.</div>
  <div class="card" style="left:346px;top:505px;width:107px;height:82px"><div class="card-icon"></div>We work in a wide range of materials, and also assist in creating fixtures for your process chain.</div>

  <svg style="left:0;top:563px" width="200" height="320" viewBox="0 0 200 320" aria-hidden="true">
    <polygon points="0,0 180,150 0,318" fill="var(--green)"/>
    <polygon points="0,40 140,150 0,280" fill="#46d400"/>
  </svg>
  <div class="product-shot" style="left:42px;top:650px;width:120px;height:185px" role="img" aria-label="3D render of the green TARN LOCK machine stop with a steel rod"></div>
  <div style="left:214px;top:630px;width:150px">
    <div class="h2">HOW WE MAKE<br>IT BETTER</div><span class="rule"></span>
    <ul class="ticks" style="margin-top:8px">
      <li>Our vast experience across multiple industries gives us insight that is invaluable in creativity and foresight.</li>
      <li>This real life experience brings a broader understanding of what works, and more importantly, what doesn't work, ultimately shortening the path to the final solution.</li>
      <li>We consider the smallest details, and envision all the consequences in order to create a better process the first time.</li>
      <li>By applying thorough risk assessment strategies we identify concerns early and address them.</li>
      <li>We maintain a culture of continuous improvement, and stay up to date with emerging technologies and techniques.</li>
    </ul>
  </div>

  <section class="caps">
    <div class="h2" style="position:absolute;left:0;right:0;top:33px;text-align:center">OUR CAPABILITIES<span class="rule center"></span></div>
    <svg style="position:absolute;left:0;top:0" width="396" height="222" viewBox="0 0 396 222" aria-hidden="true">
      <circle cx="198" cy="128" r="62" fill="none" stroke="var(--green)" stroke-width="1"/>
      <circle cx="198" cy="128" r="50" fill="#fff" stroke="#111" stroke-width="5"/>
      <g fill="#fff" stroke="var(--green)" stroke-width=".8">
        <circle cx="167" cy="73" r="8"/><circle cx="147" cy="96" r="8"/><circle cx="137" cy="126" r="8"/><circle cx="142" cy="153" r="8"/><circle cx="158" cy="175" r="8"/>
        <circle cx="231" cy="73" r="8"/><circle cx="253" cy="96" r="8" fill="var(--green)"/><circle cx="260" cy="126" r="8"/><circle cx="256" cy="153" r="8"/><circle cx="241" cy="175" r="8"/>
      </g>
      <g fill="#222"><circle cx="167" cy="73" r="2.5"/><circle cx="147" cy="96" r="2.5"/><circle cx="137" cy="126" r="2.5"/><circle cx="142" cy="153" r="2.5"/><circle cx="158" cy="175" r="2.5"/><circle cx="231" cy="73" r="2.5"/><circle cx="253" cy="96" r="2.5"/><circle cx="260" cy="126" r="2.5"/><circle cx="256" cy="153" r="2.5"/><circle cx="241" cy="175" r="2.5"/></g>
    </svg>
    <div class="head" style="position:absolute;left:148px;width:100px;top:118px;text-align:center;font-size:13px;font-weight:900;color:var(--ink)">VELKRIN</div>
    <div class="cap-label l" style="right:241px;top:70px">CAPABILITIES</div>
    <div class="cap-label l" style="right:261px;top:93px">CAD DESIGN</div>
    <div class="cap-label l" style="right:271px;top:123px">CAM PROGRAMMING</div>
    <div class="cap-label l" style="right:266px;top:150px">FFF 3D PRINTING</div>
    <div class="cap-label l" style="right:250px;top:172px">PROTOTYPES</div>
    <div class="cap-label r" style="left:243px;top:70px">VERTICAL CNC MACHINING</div>
    <div class="cap-label r" style="left:265px;top:83px;color:var(--green)">CNC TURNING<span class="cap-sub">Collet or chuck work<br>If you need parts processed through a CNC<br>lathe, let us know.</span></div>
    <div class="cap-label r" style="left:272px;top:123px">LASER MARKING</div>
    <div class="cap-label r" style="left:268px;top:147px">CONSULTING AND<br>APPLICATION ENGINEERING</div>
    <div class="cap-label r" style="left:253px;top:172px">MANUAL TURNING</div>
  </section>

  <div style="left:0;right:0;top:1099px;text-align:center"><div class="h2">OUR GALLERY</div><span class="rule center"></span><p class="small" style="margin-top:6px">Here are some of the projects we've created over the years.</p></div>
  <div class="ph" style="left:29px;top:1140px;width:66px;height:89px;background:linear-gradient(135deg,#c9b591,#6d5d44)" role="img" aria-label="Photo of brass fittings"></div>
  <div class="ph" style="left:97px;top:1140px;width:66px;height:89px;background:linear-gradient(135deg,#cfcfcf,#2c2c2c 60%,#8a8a8a)" role="img" aria-label="Photo of a machined aluminium part"></div>
  <div class="ph" style="left:165px;top:1140px;width:66px;height:89px;background:linear-gradient(135deg,#8c8c8c,#d8d8d8 50%,#555)" role="img" aria-label="Photo of a knurled metal surface"></div>
  <div class="ph" style="left:233px;top:1140px;width:66px;height:89px;background:radial-gradient(circle at 40% 40%,#b0b0b0,#3a3a3a)" role="img" aria-label="Photo of a perforated metal disc"></div>
  <div class="ph" style="left:301px;top:1140px;width:66px;height:89px;background:linear-gradient(135deg,#6e6e6e,#c0c0c0 50%,#3b3b3b)" role="img" aria-label="Photo of pyramid-textured steel"></div>

  <svg style="left:0;top:1225px" width="396" height="70" viewBox="0 0 396 70" preserveAspectRatio="none" aria-hidden="true"><polygon points="0,70 396,8 396,70" fill="#0f0f0f"/></svg>
  <footer class="footer">
    <div class="f-brand">TARN LOCK</div>
    <div class="f-col" style="left:47px"><h4>HELPFUL LINKS</h4>Why Velkrin?<br>What We Do<br>How We Make it Better<br>Capabilities<br>Gallery<br>About Us<br>Wisdom<br>Contact Us</div>
    <div class="f-col" style="left:127px"><h4>INFORMATION</h4><div class="f-soc"><i></i>Feedline</div><div class="f-soc"><i></i>Chirper</div><div class="f-soc"><i></i>Seekr</div><div class="f-soc"><i></i>Worknet</div><div class="f-soc"><i></i>Vidcast</div></div>
    <div class="f-col" style="left:195px"><h4>CONTACT US</h4><div class="f-mail"><i></i><div>Email:<br>info@tarnlock-works.com</div></div></div>
    <div class="f-col" style="left:264px"><h4>GET IN TOUCH</h4><div class="f-input">Enter Name</div><div class="f-input">Enter Company</div><div class="f-input">Enter Country</div><div class="f-submit">SUBMIT</div></div>
    <div class="f-line"></div>
    <div class="f-up">&uarr;</div>
    <div class="f-copy">© COPYRIGHT 2022 TARN LOCK, ALL RIGHTS RESERVED</div>
  </footer>
</section>

<!-- ================= GALLERY ================= -->
<section class="page page-gallery" style="left:634px;top:130px;height:658px">
  <nav class="nav">
    <div class="brand">TARN LOCK</div>
    <div class="nav-links"><span>WHY VELKRIN?</span><span>WHAT WE DO</span><span>HOW WE MAKE IT BETTER</span><span>CAPABILITIES</span><span class="on">GALLERY</span><span>ABOUT US</span><span>WISDOM</span></div>
    <div class="nav-cta">CONTACT</div>
  </nav>
  <div class="hero">
    <div class="hero-photo warm" role="img" aria-label="Photo of rows of machined metal cups"></div>
    <svg class="hero-cut" viewBox="0 0 396 135" preserveAspectRatio="none" aria-hidden="true">
      <polygon points="0,128 396,80 396,135 0,135" fill="var(--ink)"/>
      <polygon points="0,121 396,68 396,82 0,129" fill="var(--green)"/>
    </svg>
    <div class="hero-title head">GALLERY</div>
  </div>
  <div style="left:0;right:0;top:177px;text-align:center"><div class="h2">OUR PROJECTS</div><span class="rule center"></span><p class="small" style="margin-top:6px">Here are some of the projects we've created over the years.</p></div>
  <div class="grid-cell" style="left:30px;top:219px;width:65px;height:90px;background:linear-gradient(135deg,#c9b591,#6d5d44)" role="img" aria-label="Photo of brass fittings"></div>
  <div class="grid-cell" style="left:98px;top:219px;width:65px;height:90px;background:linear-gradient(135deg,#cfcfcf,#2c2c2c 60%,#8a8a8a)" role="img" aria-label="Photo of a machined aluminium part"></div>
  <div class="grid-cell" style="left:166px;top:219px;width:65px;height:90px;background:linear-gradient(135deg,#8c8c8c,#d8d8d8 50%,#555)" role="img" aria-label="Photo of a knurled metal surface"></div>
  <div class="grid-cell" style="left:234px;top:219px;width:132px;height:90px;background:linear-gradient(135deg,#4a4a4a,#b8b8b8 50%,#5a5a5a)" role="img" aria-label="Photo of a metal plate with a star cut-out"></div>
  <div class="grid-cell" style="left:30px;top:312px;width:133px;height:90px;background:linear-gradient(135deg,#9a9a9a,#3a3a3a 50%,#c4c4c4)" role="img" aria-label="Photo of metal turning chips"></div>
  <div class="grid-cell" style="left:166px;top:312px;width:65px;height:90px;background:radial-gradient(circle at 40% 40%,#b0b0b0,#3a3a3a)" role="img" aria-label="Photo of a perforated metal disc"></div>
  <div class="grid-cell" style="left:234px;top:312px;width:65px;height:90px;background:linear-gradient(150deg,#2b4e9c,#c89a5a 55%,#1f3f86)" role="img" aria-label="Photo of brass parts on a blue mat"></div>
  <div class="grid-cell" style="left:302px;top:312px;width:64px;height:90px;background:linear-gradient(135deg,#2a3d8a,#8fa0d8 50%,#1c2a66)" role="img" aria-label="Photo of blue anodised springs"></div>
  <div class="btn" style="left:181px;top:433px;width:35px;height:10px;background:#2a2a2a;color:#fff">LOAD MORE</div>

  <svg style="left:0;top:440px" width="396" height="60" viewBox="0 0 396 60" preserveAspectRatio="none" aria-hidden="true"><polygon points="0,60 396,5 396,60" fill="#0f0f0f"/></svg>
  <footer class="footer">
    <div class="f-brand">TARN LOCK</div>
    <div class="f-col" style="left:47px"><h4>HELPFUL LINKS</h4>Why Velkrin?<br>What We Do<br>How We Make it Better<br>Capabilities<br>Gallery<br>About Us<br>Wisdom<br>Contact Us</div>
    <div class="f-col" style="left:127px"><h4>INFORMATION</h4><div class="f-soc"><i></i>Feedline</div><div class="f-soc"><i></i>Chirper</div><div class="f-soc"><i></i>Seekr</div><div class="f-soc"><i></i>Worknet</div><div class="f-soc"><i></i>Vidcast</div></div>
    <div class="f-col" style="left:195px"><h4>CONTACT US</h4><div class="f-mail"><i></i><div>Email:<br>info@tarnlock-works.com</div></div></div>
    <div class="f-col" style="left:264px"><h4>GET IN TOUCH</h4><div class="f-input">Enter Name</div><div class="f-input">Enter Company</div><div class="f-input">Enter Country</div><div class="f-submit">SUBMIT</div></div>
    <div class="f-line"></div>
    <div class="f-up">&uarr;</div>
    <div class="f-copy">© COPYRIGHT 2022 TARN LOCK, ALL RIGHTS RESERVED</div>
  </footer>
</section>

<!-- ================= PRODUCT ================= -->
<section class="page page-product" style="left:634px;top:849px;height:781px">
  <nav class="nav">
    <div class="brand">TARN LOCK</div>
    <div class="nav-links"><span>WHY VELKRIN?</span><span>WHAT WE DO</span><span>HOW WE MAKE IT BETTER</span><span>CAPABILITIES</span><span>GALLERY</span><span>ABOUT US</span><span>WISDOM</span></div>
    <div class="nav-cta">CONTACT</div>
  </nav>
  <div class="hero">
    <div class="hero-photo" role="img" aria-label="Photo of a pile of steel turning chips"></div>
    <svg class="hero-cut" viewBox="0 0 396 135" preserveAspectRatio="none" aria-hidden="true">
      <polygon points="0,128 396,80 396,135 0,135" fill="var(--ink)"/>
      <polygon points="0,121 396,68 396,82 0,129" fill="var(--green)"/>
    </svg>
    <div class="hero-title head">PRODUCT</div>
  </div>
  <div style="left:30px;top:190px;width:149px;height:148px;background:var(--ink-3);border-radius:6px"></div>
  <div class="product-shot" style="left:62px;top:208px;width:85px;height:112px" role="img" aria-label="3D render of the green TARN LOCK machine stop"></div>
  <div class="product-shot" style="left:47px;top:346px;width:31px;height:31px;border-radius:2px" role="img" aria-label="Product thumbnail, front view"></div>
  <div class="product-shot" style="left:84px;top:346px;width:31px;height:31px;border-radius:2px" role="img" aria-label="Product thumbnail, side view"></div>
  <div class="product-shot" style="left:121px;top:346px;width:31px;height:31px;border-radius:2px" role="img" aria-label="Product thumbnail, top view"></div>
  <div style="left:205px;top:193px;width:165px">
    <div class="h2">PRODUCT INFO</div>
    <ul class="ticks" style="margin-top:8px;font-size:3.8px">
      <li>Fastest and most reliable setups</li>
      <li>The locating stop rod is the highest point, so cutting clearance is no longer an issue</li>
      <li>The stop rod is top-loading</li>
      <li class="sub">No need to slide it the full length to replace it</li>
      <li>You can use a wide range of shapes and sizes of stop rods</li>
      <li class="sub">This means the end user can easily and quickly use almost any item at hand</li>
      <li class="sub">No need for exact shape and size rods</li>
      <li>The clamping mechanisms do not require material deformation to function</li>
      <li>The adjustment fasteners are visible and very easy to access for quick and simple adjustments</li>
    </ul>
  </div>
  <svg style="left:200px;top:370px" width="196" height="220" viewBox="0 0 196 220" aria-hidden="true"><polygon points="196,0 196,200 40,200" fill="#262626"/></svg>
  <div class="product-shot" style="left:232px;top:392px;width:120px;height:170px" role="img" aria-label="Large 3D render of the green TARN LOCK machine stop with a steel rod"></div>
  <div style="left:35px;top:415px;width:160px">
    <ul class="ticks" style="font-size:3.8px">
      <li>Only two fasteners are needed to access the full range of movements</li>
      <li>The arm can be rotated and adjusted without changing the X-axis location</li>
      <li>The system can be mounted to many different vises, the machine table or fixture surface</li>
      <li>The design is modular to allow for easy customization or replacement. Plenty of room for chip and coolant evacuation</li>
      <li>Inherently square to the workholding for intuitive adjustments</li>
      <li>Allows for use with very small, or very large parts, as well as oddly shaped parts. Replacement parts are readily available</li>
      <li>The materials and fasteners are very common so maintenance is simple. Made in USA</li>
    </ul>
  </div>
  <div class="btn" style="left:35px;top:546px;width:56px;height:12px">SHOP NOW</div>

  <svg style="left:0;top:560px" width="396" height="60" viewBox="0 0 396 60" preserveAspectRatio="none" aria-hidden="true"><polygon points="0,60 396,10 396,60" fill="#0f0f0f"/></svg>
  <footer class="footer">
    <div class="f-brand">TARN LOCK</div>
    <div class="f-col" style="left:47px"><h4>HELPFUL LINKS</h4>Why Velkrin?<br>What We Do<br>How We Make it Better<br>Capabilities<br>Gallery<br>About Us<br>Wisdom<br>Contact Us</div>
    <div class="f-col" style="left:127px"><h4>INFORMATION</h4><div class="f-soc"><i></i>Feedline</div><div class="f-soc"><i></i>Chirper</div><div class="f-soc"><i></i>Seekr</div><div class="f-soc"><i></i>Worknet</div><div class="f-soc"><i></i>Vidcast</div></div>
    <div class="f-col" style="left:195px"><h4>CONTACT US</h4><div class="f-mail"><i></i><div>Email:<br>info@tarnlock-works.com</div></div></div>
    <div class="f-col" style="left:264px"><h4>GET IN TOUCH</h4><div class="f-input">Enter Name</div><div class="f-input">Enter Company</div><div class="f-input">Enter Country</div><div class="f-submit">SUBMIT</div></div>
    <div class="f-line"></div>
    <div class="f-up">&uarr;</div>
    <div class="f-copy">© COPYRIGHT 2022 TARN LOCK, ALL RIGHTS RESERVED</div>
  </footer>
</section>

<!-- ================= WISDOM ================= -->
<section class="page page-wisdom" style="left:170px;top:1653px;height:703px">
  <nav class="nav">
    <div class="brand">TARN LOCK</div>
    <div class="nav-links"><span>WHY VELKRIN?</span><span>WHAT WE DO</span><span>HOW WE MAKE IT BETTER</span><span>CAPABILITIES</span><span>GALLERY</span><span>ABOUT US</span><span class="on">WISDOM</span></div>
    <div class="nav-cta">CONTACT</div>
  </nav>
  <div class="hero">
    <div class="hero-photo warm" role="img" aria-label="Photo of rows of threaded metal inserts"></div>
    <svg class="hero-cut" viewBox="0 0 396 135" preserveAspectRatio="none" aria-hidden="true">
      <polygon points="0,128 396,80 396,135 0,135" fill="var(--ink)"/>
      <polygon points="0,121 396,68 396,82 0,129" fill="var(--green)"/>
    </svg>
    <div class="hero-title head">WISDOM</div>
  </div>
  <svg style="left:40px;top:185px" width="140" height="145" viewBox="0 0 140 145" aria-hidden="true"><polygon points="70,0 140,72 70,145 0,72" fill="#262626"/></svg>
  <div class="product-shot" style="left:72px;top:200px;width:78px;height:118px" role="img" aria-label="3D render of the green TARN LOCK machine stop"></div>
  <div style="left:218px;top:204px;width:150px">
    <div class="h2">WISDOM</div>
    <div class="head" style="font-size:4.4px;margin-top:7px">SHORT AND SWEET ADVICE</div>
    <p class="small" style="margin-top:5px">You didn't come this far, to only come this far.</p>
    <p class="small" style="margin-top:4px">Sometimes you come across a great quote that gives you a bit of clarity otherwise not considered. These are a few that we've come across and think are worth sharing.</p>
    <p class="small" style="margin-top:4px">If you have one you'd like to see added to the list, let us know!</p>
  </div>
  <div class="h2" style="left:0;right:0;top:360px;text-align:center">WORDS OF WISDOM<span class="rule center"></span></div>
  <div class="arrow-btn on" style="left:332px;top:361px">&larr;</div>
  <div class="arrow-btn" style="left:352px;top:361px">&rarr;</div>
  <div class="quote" style="left:36px;top:392px;width:107px;height:80px"><div class="quote-mark">&ldquo;</div><p>Sometimes the shortcut is the long way.</p><cite>- Japanese Wisdom</cite></div>
  <div class="quote" style="left:145px;top:392px;width:107px;height:80px"><div class="quote-mark">&ldquo;</div><p>No problem can withstand the assault of sustained thinking.</p><cite>- Fortune Cookie</cite></div>
  <div class="quote" style="left:255px;top:392px;width:107px;height:80px"><div class="quote-mark">&ldquo;</div><p>If you're picky, you go without.</p><cite>- Grandpa</cite></div>

  <svg style="left:0;top:480px" width="396" height="60" viewBox="0 0 396 60" preserveAspectRatio="none" aria-hidden="true"><polygon points="0,60 396,10 396,60" fill="#0f0f0f"/></svg>
  <footer class="footer">
    <div class="f-brand">TARN LOCK</div>
    <div class="f-col" style="left:47px"><h4>HELPFUL LINKS</h4>Why Velkrin?<br>What We Do<br>How We Make it Better<br>Capabilities<br>Gallery<br>About Us<br>Wisdom<br>Contact Us</div>
    <div class="f-col" style="left:127px"><h4>INFORMATION</h4><div class="f-soc"><i></i>Feedline</div><div class="f-soc"><i></i>Chirper</div><div class="f-soc"><i></i>Seekr</div><div class="f-soc"><i></i>Worknet</div><div class="f-soc"><i></i>Vidcast</div></div>
    <div class="f-col" style="left:195px"><h4>CONTACT US</h4><div class="f-mail"><i></i><div>Email:<br>info@tarnlock-works.com</div></div></div>
    <div class="f-col" style="left:264px"><h4>GET IN TOUCH</h4><div class="f-input">Enter Name</div><div class="f-input">Enter Company</div><div class="f-input">Enter Country</div><div class="f-submit">SUBMIT</div></div>
    <div class="f-line"></div>
    <div class="f-up">&uarr;</div>
    <div class="f-copy">© COPYRIGHT 2022 TARN LOCK, ALL RIGHTS RESERVED</div>
  </footer>
</section>

<!-- ================= CONTACT ================= -->
<section class="page page-contact" style="left:634px;top:1699px;height:707px">
  <nav class="nav">
    <div class="brand">TARN LOCK</div>
    <div class="nav-links"><span>WHY VELKRIN?</span><span>WHAT WE DO</span><span>HOW WE MAKE IT BETTER</span><span>CAPABILITIES</span><span>GALLERY</span><span>ABOUT US</span><span>WISDOM</span></div>
    <div class="nav-cta">CONTACT</div>
  </nav>
  <div class="hero">
    <div class="hero-photo warm" role="img" aria-label="Photo of rows of threaded metal inserts"></div>
    <svg class="hero-cut" viewBox="0 0 396 135" preserveAspectRatio="none" aria-hidden="true">
      <polygon points="0,128 396,80 396,135 0,135" fill="var(--ink)"/>
      <polygon points="0,121 396,68 396,82 0,129" fill="var(--green)"/>
    </svg>
    <div class="hero-title head">CONTACT</div>
  </div>
  <div style="left:0;right:0;top:167px;text-align:center"><div class="h2">GET IN TOUCH</div><span class="rule center"></span><p class="small" style="margin-top:6px">Please fill out the information below to complete...</p></div>

  <div class="c-item" style="left:64px;top:219px">
    <div class="c-icon"><svg width="10" height="10" viewBox="0 0 24 24"><path d="M6.6 10.8a15.1 15.1 0 0 0 6.6 6.6l2.2-2.2a1 1 0 0 1 1-.25 11.4 11.4 0 0 0 3.6.57 1 1 0 0 1 1 1V20a1 1 0 0 1-1 1A17 17 0 0 1 3 4a1 1 0 0 1 1-1h3.5a1 1 0 0 1 1 1c0 1.25.2 2.45.57 3.57a1 1 0 0 1-.25 1z" fill="#141414"/></svg></div>
    <div><span>Phone:</span><b>612 555 0148</b></div>
  </div>
  <div class="c-item" style="left:64px;top:248px">
    <div class="c-icon"><svg width="10" height="10" viewBox="0 0 24 24"><path d="M3 5h18v14H3z" fill="#141414"/><path d="M3 5l9 7 9-7" fill="none" stroke="#59ff00" stroke-width="1.6"/></svg></div>
    <div><span>Email:</span><b>info@tarnlock-works.com</b></div>
  </div>
  <div class="c-item" style="left:64px;top:280px">
    <div class="c-icon"><svg width="10" height="10" viewBox="0 0 24 24"><path d="M12 2a7 7 0 0 0-7 7c0 5 7 13 7 13s7-8 7-13a7 7 0 0 0-7-7z" fill="#141414"/><circle cx="12" cy="9" r="2.5" fill="#59ff00"/></svg></div>
    <div><span>Address:</span><b>Some goes address here</b></div>
  </div>

  <div class="f-label" style="left:198px;top:216px">NAME*</div>
  <div class="f-label" style="left:266px;top:216px">EMAIL*</div>
  <div class="c-field" style="left:198px;top:223px;width:65px;height:13px">Enter your name</div>
  <div class="c-field" style="left:266px;top:223px;width:65px;height:13px">Enter your email</div>
  <div class="f-label" style="left:198px;top:239px">PHONE*</div>
  <div class="f-label" style="left:266px;top:239px">DATE*</div>
  <div class="c-field" style="left:198px;top:246px;width:65px;height:13px">Enter phone number</div>
  <div class="c-field" style="left:266px;top:246px;width:65px;height:13px">Select date</div>
  <div class="f-label" style="left:198px;top:262px">PHONE*</div>
  <div class="c-field" style="left:198px;top:269px;width:133px;height:37px;align-items:flex-start;padding-top:4px">Type your text...</div>
  <div class="btn" style="left:198px;top:317px;width:133px;height:15px;font-size:4px">SUBMIT NOW</div>

  <div style="left:63px;top:364px;width:269px;height:121px;background:linear-gradient(135deg,#e4e4e4,#cfcfcf);border:3px solid #2a2a2a;border-radius:3px" role="img" aria-label="Street map showing the company location"></div>
  <svg style="left:193px;top:414px" width="10" height="14" viewBox="0 0 24 32" aria-hidden="true"><path d="M12 0a10 10 0 0 0-10 10c0 7 10 22 10 22s10-15 10-22A10 10 0 0 0 12 0z" fill="#141414"/><circle cx="12" cy="10" r="4" fill="#e4e4e4"/></svg>

  <svg style="left:0;top:480px" width="396" height="60" viewBox="0 0 396 60" preserveAspectRatio="none" aria-hidden="true"><polygon points="0,60 396,10 396,60" fill="#0f0f0f"/></svg>
  <footer class="footer">
    <div class="f-brand">TARN LOCK</div>
    <div class="f-col" style="left:47px"><h4>HELPFUL LINKS</h4>Why Velkrin?<br>What We Do<br>How We Make it Better<br>Capabilities<br>Gallery<br>About Us<br>Wisdom<br>Contact Us</div>
    <div class="f-col" style="left:127px"><h4>INFORMATION</h4><div class="f-soc"><i></i>Feedline</div><div class="f-soc"><i></i>Chirper</div><div class="f-soc"><i></i>Seekr</div><div class="f-soc"><i></i>Worknet</div><div class="f-soc"><i></i>Vidcast</div></div>
    <div class="f-col" style="left:195px"><h4>CONTACT US</h4><div class="f-mail"><i></i><div>Email:<br>info@tarnlock-works.com</div></div></div>
    <div class="f-col" style="left:264px"><h4>GET IN TOUCH</h4><div class="f-input">Enter Name</div><div class="f-input">Enter Company</div><div class="f-input">Enter Country</div><div class="f-submit">SUBMIT</div></div>
    <div class="f-line"></div>
    <div class="f-up">&uarr;</div>
    <div class="f-copy">© COPYRIGHT 2022 TARN LOCK, ALL RIGHTS RESERVED</div>
  </footer>
</section>

</body>
</html>
```